Need a new company business card

I am looking for a new company business card. Front and back. With information on it as per below. Card should be professional. Yet clever. Simple. Modern design. Pim card, traditional size. OK with say, all black or all red backside.

Varnholt is an indie, bootstrapped magazine advancing the work of intersectional feminists busting their buts to create a just world through the power of enterprise and innovation.

Varnholt is the home and voice of entrepreneurial feminism and feminist innovators worldwide. Entrepreneurial feminists are people (of all genders) who see inequality as an innovation priority. They work to advance gender equity and/or who strive to integrate and practice feminist principles, pedagogy, values into their innovation and entrepreneurship work.
We are committed to this space being trans and queer inclusive, anti-racist, intersectional, brave, and safe. We welcome all allies. We value learning, edgy but civil discourse and integrative thinking skills.

Target Market(s)

feminists, business owners,

Industry/Entity Type

Publishing Company

Contact Information for Business Card

RD Tolliver
Founder/Publisher
4-237 Ashgrove Lane, Toronto, ON
M4T 2K8
publisher@varnholt.com
416-552-3019
www.varnholt.com

Font styles to use
Serif
Other font styles liked:
• Myriad Pro

Colors
ec1f27
000000
ffffff

Requirements
Must have
• logo
• use red, black white colours only.
Nice to have
• use the compass in pattern or creatively but not too busy please
Should not have
• Should not be too busy. Elegant.

```html
<!DOCTYPE html>
<html lang="en">
<head>
<meta charset="utf-8">
<title>Varnholt – Business Card</title>
<link rel="stylesheet" href="https://fonts.googleapis.com/css2?family=Roboto:wght@400;500;700&display=swap">
<style>
  :root {
    --brand-red: #d9272e;
    --ink: #2a2a2a;
    --card-surface: #eeeceb;
    --card-edge: #d8d5d2;
    --backdrop: #e2ddd8;
  }
  * { margin: 0; padding: 0; box-sizing: border-box; }
  html, body {
    width: 1200px;
    height: 1054px;
    overflow: hidden;
    background: var(--backdrop);
    font-family: "Roboto", Arial, sans-serif;
  }
  .card {
    position: absolute;
    left: 150px;
    top: 255px;
    width: 900px;
    height: 544px;
    background: var(--card-surface);
    border: 1px solid var(--card-edge);
    color: var(--ink);
  }
  .brand {
    position: absolute;
    left: 92px;
    top: 222px;
    width: 300px;
    font-size: 46px;
    font-weight: 700;
    color: var(--brand-red);
    letter-spacing: 0.5px;
  }
  .identity {
    position: absolute;
    left: 491px;
    top: 155px;
  }
  .identity .name {
    font-size: 32px;
    font-weight: 700;
    line-height: 1.15;
  }
  .identity .role {
    margin-top: 6px;
    font-size: 21px;
    color: var(--brand-red);
  }
  .contacts {
    position: absolute;
    left: 500px;
    top: 262px;
    list-style: none;
  }
  .contacts li {
    display: flex;
    align-items: center;
    height: 29px;
    font-size: 21px;
  }
  .contacts svg {
    width: 17px;
    height: 17px;
    margin-right: 17px;
    fill: var(--brand-red);
    flex: none;
  }
  .address {
    position: absolute;
    left: 216px;
    top: 495px;
    font-size: 20px;
  }
</style>
</head>
<body>
  <div class="card">
    <div class="brand">Varnholt</div>

    <div class="identity">
      <div class="name">RD Tolliver</div>
      <div class="role">Founder/Publisher</div>
    </div>

    <ul class="contacts">
      <li>
        <svg viewBox="0 0 16 16" aria-hidden="true"><path d="M2 6c0-2 2-3.5 6-3.5S14 4 14 6v1h-3V5.6C10.3 5.3 9.2 5.2 8 5.2s-2.3.1-3 .4V7H2zM4 8h8l2 3v3H2v-3zm4 1.3a1.7 1.7 0 1 0 0 3.4 1.7 1.7 0 0 0 0-3.4z"/></svg>
        416-552-3019
      </li>
      <li>
        <svg viewBox="0 0 16 16" aria-hidden="true"><path d="M1 3h14v1.2L8 9 1 4.2zM1 5.8l7 4.8 7-4.8V13H1z"/></svg>
        publisher@varnholt.com
      </li>
      <li>
        <svg viewBox="0 0 16 16" aria-hidden="true" fill="none"><g fill="none" stroke="#d9272e" stroke-width="1.4"><circle cx="8" cy="8" r="6.3"/><ellipse cx="8" cy="8" rx="2.7" ry="6.3"/><path d="M1.7 8h12.6M3 4.6h10M3 11.4h10"/></g></svg>
        www.varnholt.com
      </li>
    </ul>

    <div class="address">4-237 Ashgrove Lane, Toronto, ON M4T 2K8</div>
  </div>
</body>
</html>
```